Business Card Update, need to bring life to the card, two sided color

We need a new business card design, are moving and changing addresses and need a new look, we have the logos already attached but need a new style moving forward. Can incorporate the color of the logo (The Green) as well, maybe a solid back? We deal with safety products revolving around static electricity and safety lighting. Would like to keep same font in second logo as well.

Target Market(s)

Electrical Safety, Lighting

Contact Information for Business Card

Dale Fenwick
Vice President
Office: 770-555-4821
Cell: 770-555-3067
dale@tkfenwick.example
www.tkfenwick.example
4700 West Harbor Boulevard
Suite #150
Roswell, GA 30076

Font styles to use
Serif
Sans Serif

Requirements
Must have
• Since 1918
Nice to have
• Could use the 100 Year Logo for back of card, would like the back of card to be the same green as logo.
Should not have
• No black cards please.

```html
<!DOCTYPE html>
<html lang="en">
<head>
<meta charset="utf-8">
<title>T.K. Fenwick Business Card</title>
<link href="https://fonts.googleapis.com/css2?family=Arimo:wght@400;700&family=Source+Sans+3:wght@400&display=swap" rel="stylesheet">
<style>
  :root {
    --brand-green: #00965a;
    --ink: #111111;
    --paper: #ffffff;
    --backdrop: #f5f5ef;
    --frame: #2a2a2a;
    --rule-grey: #b3b3b3;
  }
  * { margin: 0; padding: 0; box-sizing: border-box; }
  html, body { width: 1200px; height: 862px; overflow: hidden; }
  body { background: var(--backdrop); }
  .canvas {
    position: relative; width: 1200px; height: 862px;
    background: var(--backdrop);
    border: 4px solid var(--frame);
  }
  .card { position: absolute; overflow: hidden; border-radius: 36px; }
  .card-front {
    left: 52px; top: 21px; width: 683px; height: 391px;
    background: var(--paper);
    border: 1px solid #333;
  }
  .card-back {
    left: 460px; top: 436px; width: 676px; height: 384px;
    background: var(--brand-green);
  }
  .wave { position: absolute; left: 0; top: 0; width: 100%; height: 100%; }
  .brand-mark { position: absolute; border-radius: 50%; }
  .front-mark { left: 53px; top: 126px; width: 82px; height: 82px; background: var(--brand-green); }
  .back-mark { left: 36px; top: 107px; width: 142px; height: 142px; background: var(--ink); }
  .brand-name, .brand-sub, .brand-since, .person-name, .person-title, .back-url {
    position: absolute; font-family: "Arimo", Arial, sans-serif; font-weight: 700; white-space: nowrap;
  }
  .front-brand-name { left: 140px; top: 139px; font-size: 27px; color: var(--brand-green); }
  .front-brand-sub { left: 158px; top: 172px; font-size: 13.5px; color: var(--brand-green); }
  .front-since { left: 158px; top: 191px; font-size: 12px; color: var(--brand-green); letter-spacing: 1px; }
  .divider { position: absolute; left: 403px; top: 100px; width: 2px; height: 186px; background: var(--rule-grey); }
  .contact {
    position: absolute; left: 418px; top: 100px;
    font-family: "Source Sans 3", "Myriad Pro", sans-serif; font-size: 16px; color: var(--ink); line-height: 20px;
  }
  .contact .address { margin-bottom: 8px; }
  .contact .line { display: flex; align-items: center; gap: 5px; height: 26px; }
  .contact svg { width: 14px; height: 14px; flex: none; }
  .person-name { left: 69px; top: 326px; font-size: 25px; color: var(--paper); }
  .person-title { left: 69px; top: 357px; font-size: 19px; color: var(--ink); }
  .back-brand-name { left: 185px; top: 142px; font-size: 50px; color: var(--ink); }
  .back-brand-sub { left: 214px; top: 200px; font-size: 24px; color: var(--ink); }
  .back-since { left: 214px; top: 234px; font-size: 18px; color: var(--ink); letter-spacing: 2px; }
  .back-url { left: 188px; top: 351px; font-size: 20px; font-weight: 400; letter-spacing: 4px; color: var(--ink); }
</style>
</head>
<body>
<div class="canvas">
  <section class="card card-front" aria-label="Card front">
    <svg class="wave" viewBox="0 0 754 431" preserveAspectRatio="none" aria-hidden="true">
      <path d="M0,357 C150,338 250,345 420,380 C560,410 680,402 754,392 L754,431 L0,431 Z" fill="var(--brand-green)"/>
      <path d="M0,349 C120,326 240,330 330,352" fill="none" stroke="var(--brand-green)" stroke-width="5"/>
      <path d="M160,324 C320,318 470,392 754,382" fill="none" stroke="var(--rule-grey)" stroke-width="2"/>
      <path d="M400,355 C520,384 650,384 754,356 L754,376 C650,393 520,390 400,355 Z" fill="var(--ink)"/>
    </svg>
    <div class="brand-mark front-mark"></div>
    <div class="brand-name front-brand-name">T.K. Fenwick</div>
    <div class="brand-sub front-brand-sub">Manufacturing Company, Inc.</div>
    <div class="brand-since front-since">SINCE 1918</div>
    <div class="divider"></div>
    <div class="contact">
      <div class="address">4700 West Harbor Boulevard<br>Suite #150<br>Roswell, GA 30076</div>
      <div class="line">
        <svg viewBox="0 0 16 16"><circle cx="8" cy="8" r="7" fill="none" stroke="var(--brand-green)" stroke-width="1.5"/><path d="M5.5,4.5 L7,4.5 L7.5,6.5 L6.6,7.2 C7.1,8.3 7.8,9 8.8,9.4 L9.5,8.5 L11.5,9 L11.5,10.5 C8,11 5,8 5.5,4.5 Z" fill="var(--brand-green)"/></svg>
        <span>Office: 770-555-4821</span>
      </div>
      <div class="line">
        <svg viewBox="0 0 16 16"><circle cx="8" cy="8" r="7" fill="none" stroke="var(--brand-green)" stroke-width="1.5"/><rect x="5.5" y="3.8" width="5" height="8.4" rx="1" fill="none" stroke="var(--brand-green)" stroke-width="1.2"/><circle cx="8" cy="10.4" r="0.7" fill="var(--brand-green)"/></svg>
        <span>Cell: 770-555-3067</span>
      </div>
      <div class="line">
        <svg viewBox="0 0 16 16"><circle cx="8" cy="8" r="6.5" fill="none" stroke="var(--brand-green)" stroke-width="1.3"/><ellipse cx="8" cy="8" rx="3" ry="6.5" fill="none" stroke="var(--brand-green)" stroke-width="1"/><path d="M1.5,8 H14.5 M2.5,5 H13.5 M2.5,11 H13.5" stroke="var(--brand-green)" stroke-width="1"/></svg>
        <span>www.tkfenwick.example</span>
      </div>
      <div class="line">
        <svg viewBox="0 0 16 16"><circle cx="8" cy="8" r="7" fill="none" stroke="var(--brand-green)" stroke-width="1.5"/><rect x="4" y="5.5" width="8" height="5.5" fill="none" stroke="var(--brand-green)" stroke-width="1.2"/><path d="M4,5.5 L8,8.8 L12,5.5" fill="none" stroke="var(--brand-green)" stroke-width="1.2"/></svg>
        <span>dale@tkfenwick.example</span>
      </div>
    </div>
    <div class="person-name">Dale Fenwick</div>
    <div class="person-title">Vice President</div>
  </section>

  <section class="card card-back" aria-label="Card back">
    <div class="brand-mark back-mark"></div>
    <div class="brand-name back-brand-name">T.K. Fenwick</div>
    <div class="brand-sub back-brand-sub">Manufacturing Company, Inc.</div>
    <div class="brand-since back-since">SINCE 1918</div>
    <div class="back-url">www.tkfenwick.example</div>
  </section>
</div>
</body>
</html>
```